Doctor Formulated Medical Cosmetics

Velour Skinhaus is an E-commerce site for high end Medical Cosmetics designed to treat specific skin problems. The Velour Skinhaus difference/advantage is that all creams and serums are:
Doctor Formulated, Freshly Handmade, Registered Pharmacy.
The Site also provides real doctor Dermatology Consultations, Library (with a list of - 1. Active Ingredients in the creams with description of their effects, 2. Skin Conditions with information on what causes the condition and typical treatment approaches and outcomes. 3. Resources from Dermatology Journals and literature on the conditions.)
Header Information: Velour Skinhaus, languages EN, BG, Register / log in, Shopping Bag. This field should be narrow.
Categories (horizontal): Home, Face, Body, Hair Care, Skin Conditions, Doctor Consultation, Library
The Landing Page should have only one well organized picture, which is intended to create the feeling of luxury, freedom and relaxation. It will be large and will fill the whole screen. All text should be on transparent or similar color fields. Please use the color of the text to create also the feeling of conservative luxury.
Written message / image overlay Velour Skinhaus(logo), Skin Care, Doctor Formulated, Freshly Handmade, Registered Pharmacy.
Please study the Landing Page of this site as an example: www.marivane.com
Under the Landing Page, there should be a slider with 4 of our products.
Underneath: Four Blog Articles (large pictures for maximum impact and luxury text underneath).
Underneath: Banner for Dermatologist Consultation, (button for Start Your Case Now).
Underneath: Two pictures in a line - Library (with books), and Active Ingredients.
Footer: Philosophy, Categories, Customer Care
Please adhere to the color palate provided in the pictures (as attachments). Provided are some examples of Web Sites with the desired look and feel. www.quillora.com , www.tavenholtmd.com .
Please use different shades of gray, white, beige and gold colors, and black. Our products will be in brown glass jars and bottles to convey the professional, pharmacy made nature of the creams and lotions.
We find the following Front Page very attractive and effective - www.marivane.com , with its full page image and overlaying text.
Please have a look at this link for the Landing page.
http://www.brimlensphoto.com/detail/video/woman-lying-on-a-black-sand-beach-in-a-bikini-stock-footage/58213067
I would like to use it in the animated version to achieve the WOW effect. I have uploaded the jpeg version for it, so you will be able create your design.
For the Landing page design, please use only the two uploaded pictures of a woman laying at the beach. Let's see how each of them will look like.
Thank you for your help.

```html
<!DOCTYPE html>
<html lang="en">
<head>
<meta charset="utf-8">
<title>Velour Skinhaus — Doctor Formulated Medical Cosmetics</title>
<link rel="stylesheet" href="https://fonts.googleapis.com/css2?family=Jost:wght@400;500;600&family=Raleway:wght@400;500;600;700&display=swap">
<style>
  :root{
    --taupe:#a99b8f;
    --ink:#1f1c18;
    --gold:#c9a84a;
    --gold-text:#c3a042;
    --product-name:#9c8a76;
    --grey-bg:#efefef;
    --grey-text:#8a8a8a;
    --dark-text:#333;
    --line:#dcdcdc;
    --white:#fff;
  }
  *{box-sizing:border-box;margin:0;padding:0}
  html,body{width:1200px;height:2848px;overflow:hidden;background:var(--white)}
  body{position:relative;font-family:"Raleway",sans-serif;color:var(--dark-text)}
  .abs{position:absolute}

  /* utility bar */
  .utility-bar{top:0;left:0;width:1200px;height:46px;background:var(--taupe);color:var(--white);font-family:"Jost",sans-serif;font-size:16px}
  .utility-bar .lang{left:146px;top:11px}
  .utility-bar .account{right:128px;top:11px}
  .utility-bar .bag{right:92px;top:8px}

  /* main navigation */
  .main-nav{top:46px;left:0;width:1200px;height:131px;background:var(--ink)}
  .brand{left:148px;top:44px;color:var(--gold);font-family:"Jost",sans-serif;font-size:36px;font-weight:400;letter-spacing:.5px;line-height:44px}
  .nav-item{top:0;height:131px;border-left:1px solid #3e3a34;color:var(--white);font-family:"Jost",sans-serif;font-size:15px;text-align:center;line-height:1.15;display:flex;flex-direction:column;align-items:center;justify-content:flex-start;padding-top:28px}
  .nav-item.last{border-right:1px solid #3e3a34}
  .nav-item svg{margin-bottom:10px}

  /* hero */
  .hero{top:177px;left:0;width:1200px;height:480px;background:linear-gradient(160deg,#b6aca1 0%,#d8d1c8 35%,#cfc7bd 60%,#9f978c 100%)}
  .hero-brand{top:115px;left:0;width:1200px;text-align:center;color:var(--white);font-family:"Jost",sans-serif;font-size:48px;line-height:60px}
  .hero-tagline{top:198px;left:0;width:1200px;text-align:center;color:var(--white);font-family:"Jost",sans-serif;font-size:32px;line-height:44px}
  .hero-dots{top:436px;left:558px;display:flex;gap:6px}
  .hero-dots span{width:16px;height:16px;border-radius:50%;background:var(--white)}
  .hero-dots span.active{background:transparent;border:2px solid var(--white)}

  /* products */
  .products{top:657px;left:0;width:1200px;height:384px;background:var(--grey-bg)}
  .section-title{font-family:"Jost",sans-serif;color:var(--dark-text);font-weight:400}
  .products .section-title{top:36px;width:1200px;text-align:center;font-size:25px}
  .product{top:93px;width:238px;text-align:center}
  .product .shot{margin:0 auto;width:170px;height:170px}
  .product .name{margin-top:12px;font-family:"Jost",sans-serif;font-size:20px;line-height:24px;color:var(--product-name)}
  .product .sub{margin-top:4px;font-size:14px;line-height:18px;color:var(--grey-text)}
  .product-divider{top:93px;width:1px;height:253px;background:var(--line)}

  /* blogs */
  .blogs-title{top:1088px;left:154px;font-size:27px;line-height:32px}
  .blog-card{width:288px;height:271px;border:1px solid var(--line);background:var(--white);text-align:center}
  .blog-card .photo{position:absolute;left:10px;top:9px;width:266px;height:137px}
  .blog-card .date{position:absolute;left:93px;top:128px;width:102px;height:24px;background:var(--gold);color:var(--white);font-size:11px;line-height:24px;font-weight:600}
  .blog-card .title{position:absolute;top:166px;width:100%;font-size:17px;line-height:22px;color:var(--gold-text);font-weight:500}
  .blog-card .excerpt{position:absolute;top:190px;left:20px;width:248px;font-size:11px;line-height:18px;color:var(--grey-text)}
  .blog-card .more{position:absolute;top:234px;width:100%;font-size:13px;line-height:16px;color:var(--dark-text);font-weight:600}

  /* consultation banner */
  .consult{top:1734px;left:0;width:1200px;height:355px;background:linear-gradient(100deg,#b4c6e6 0%,#cfdbef 45%,#dfe7f5 70%,#c9d6ee 100%)}
  .consult .model{left:640px;top:0;width:420px;height:355px;background:radial-gradient(ellipse at 55% 45%,#e9d6b8 0%,#d9c7ad 40%,rgba(210,220,238,0) 72%)}
  .consult .brand-line{top:88px;left:154px;color:var(--white);font-family:"Jost",sans-serif;font-size:50px;line-height:60px}
  .consult h2{top:168px;left:156px;font-family:"Jost",sans-serif;font-weight:600;font-size:28px;line-height:36px;color:var(--ink)}
  .consult p{top:211px;left:156px;width:440px;font-family:"Jost",sans-serif;font-size:20px;line-height:28px;color:#555}

  /* articles */
  .articles-title{top:2141px;width:1200px;text-align:center;font-size:31px;line-height:38px}
  .article{top:2200px;width:438px}
  .article .photo{width:438px;height:193px;border:1px solid var(--line)}
  .article .title{margin-top:22px;font-family:"Jost",sans-serif;font-size:21px;line-height:26px;color:var(--dark-text)}
  .article .body{margin-top:4px;font-family:"Jost",sans-serif;font-size:15px;line-height:23px;color:#666}

  /* footer */
  .footer{top:2557px;left:0;width:1200px;height:291px;background:var(--gold)}
  .footer h4{font-family:"Raleway",sans-serif;font-size:13px;font-weight:700;color:var(--white);letter-spacing:.5px;line-height:16px}
  .footer .links a{display:block;color:var(--white);font-size:12px;text-decoration:none;line-height:28.5px}
  .socials{top:64px;left:480px;display:flex;gap:10px}
  .socials span{width:34px;height:34px;border-radius:50%;background:var(--ink)}
  .newsletter-note{top:77px;left:722px;color:var(--white);font-size:12px}
  .subscribe{top:99px;left:722px;display:flex}
  .subscribe .field{width:201px;height:34px;background:var(--white);font-size:11px;color:#555;line-height:34px;padding-left:10px;font-weight:600}
  .subscribe .button{width:95px;height:34px;background:#111;color:var(--white);font-size:12px;font-weight:700;line-height:34px;text-align:center}
  .cards{top:154px;left:722px;display:flex;gap:10px}
  .cards span{width:38px;height:22px;background:var(--white);border-radius:2px}
  .footer-rule{top:232px;left:148px;width:904px;height:1px;background:rgba(255,255,255,.35)}
  .copyright{top:251px;width:1200px;text-align:center;color:var(--white);font-size:11px}
</style>
</head>
<body>

<header class="utility-bar abs">
  <div class="lang abs">Language: EN &nbsp;|&nbsp; BG</div>
  <div class="account abs">Doctor &nbsp;|&nbsp; Pharmacy &nbsp;|&nbsp; Register &nbsp;|&nbsp; Log In</div>
  <svg class="bag abs" width="24" height="28" viewBox="0 0 24 28" aria-label="Shopping bag">
    <path d="M7 9V6a5 5 0 0 1 10 0v3" fill="none" stroke="#fff" stroke-width="2"/>
    <rect x="2" y="9" width="20" height="18" rx="1" fill="#fff"/>
  </svg>
</header>

<nav class="main-nav abs">
  <div class="brand abs">Velour Skinhaus</div>
  <div class="nav-item abs" style="left:463px;width:75px">
    <svg width="30" height="30" viewBox="0 0 30 30"><path d="M8 26c0-10 6-18 16-20M12 26c0-7 4-13 12-15" fill="none" stroke="#c9a84a" stroke-width="2"/></svg>Face</div>
  <div class="nav-item abs" style="left:538px;width:74px">
    <svg width="30" height="30" viewBox="0 0 30 30"><path d="M10 4v8c0 4 2 6 5 6s5-2 5-6V4M9 26l6-8 6 8" fill="none" stroke="#c9a84a" stroke-width="2"/></svg>Body</div>
  <div class="nav-item abs" style="left:612px;width:110px">
    <svg width="30" height="30" viewBox="0 0 30 30"><path d="M11 3v24M19 3v24M11 10h8" fill="none" stroke="#c9a84a" stroke-width="2"/></svg>Hair Care</div>
  <div class="nav-item abs" style="left:722px;width:108px">
    <svg width="30" height="30" viewBox="0 0 30 30"><circle cx="15" cy="13" r="9" fill="none" stroke="#c9a84a" stroke-width="2"/><path d="M10 27h10" stroke="#c9a84a" stroke-width="2"/></svg>Skin<br>Concerns</div>
  <div class="nav-item abs" style="left:830px;width:139px">
    <svg width="30" height="30" viewBox="0 0 30 30"><path d="M4 24h22M8 24V12M15 24V8M22 24V14" fill="none" stroke="#c9a84a" stroke-width="2"/></svg>Dermatologist<br>Consultation</div>
  <div class="nav-item last abs" style="left:969px;width:91px">
    <svg width="30" height="30" viewBox="0 0 30 30"><path d="M4 10l11-5 11 5-11 5zM4 15l11 5 11-5M4 20l11 5 11-5" fill="none" stroke="#c9a84a" stroke-width="2"/></svg>Library</div>
</nav>

<section class="hero abs" role="img" aria-label="Woman relaxing in sunglasses and swimsuit on a white lounge deck">
  <div class="hero-brand abs">Velour Skinhaus</div>
  <div class="hero-tagline abs">Doctor Formulated, Freshly Handmade,<br>Registered Pharmacy &amp; Highest Ethical Standard</div>
  <div class="hero-dots abs"><span class="active"></span><span></span><span></span><span></span></div>
</section>

<section class="products abs">
  <h2 class="section-title abs">OUR PRODUCTS</h2>
  <div class="product abs" style="left:130px">
    <div class="shot" role="img" aria-label="Product photo: brown lotion bottle" style="background:linear-gradient(#efefef,#d9c6b2 50%,#efefef)"></div>
    <div class="name">Product Name</div><div class="sub">Sociosqu litora torquent</div></div>
  <div class="product-divider abs" style="left:366px"></div>
  <div class="product abs" style="left:368px">
    <div class="shot" role="img" aria-label="Product photo: cream jar" style="background:linear-gradient(#efefef,#e2cfbb 50%,#efefef)"></div>
    <div class="name">Product Name</div><div class="sub">Sociosqu litora torquent</div></div>
  <div class="product-divider abs" style="left:606px"></div>
  <div class="product abs" style="left:607px">
    <div class="shot" role="img" aria-label="Product photo: serum pump bottle" style="background:linear-gradient(#efefef,#e4d4c4 50%,#efefef)"></div>
    <div class="name">Product Name</div><div class="sub">Sociosqu litora torquent</div></div>
  <div class="product-divider abs" style="left:843px"></div>
  <div class="product abs" style="left:845px">
    <div class="shot" role="img" aria-label="Product photo: white cream jar with gold lid" style="background:linear-gradient(#efefef,#dcd3c0 50%,#efefef)"></div>
    <div class="name">Product Name</div><div class="sub">Sociosqu litora torquent</div></div>
</section>

<h2 class="section-title blogs-title abs">LATEST BLOGS</h2>

<article class="blog-card abs" style="left:154px;top:1139px">
  <div class="photo" role="img" aria-label="Blonde woman portrait" style="background:linear-gradient(90deg,#d9b896,#8a6a52 60%,#1e1e1e)"></div>
  <div class="date">02 MAY 2016</div><div class="title">Aculis facilisis massa</div>
  <div class="excerpt">Etiam eu urna Sed porta Suspendisse quam leo molestie sed luctus quis feugiat</div><div class="more">Read More</div></article>
<article class="blog-card abs" style="left:457px;top:1139px">
  <div class="photo" role="img" aria-label="Woman relaxing with eyes closed" style="background:linear-gradient(90deg,#9c8a7c,#e4c9b0 55%,#b7a393)"></div>
  <div class="date">02 MAY 2016</div><div class="title">Aculis facilisis massa</div>
  <div class="excerpt">Etiam eu urna Sed porta Suspendisse quam leo molestie sed luctus quis feugiat</div><div class="more">Read More</div></article>
<article class="blog-card abs" style="left:759px;top:1139px">
  <div class="photo" role="img" aria-label="Close-up of a couple about to kiss" style="background:linear-gradient(90deg,#5b3a32,#b07b68 50%,#d9c0b5)"></div>
  <div class="date">02 MAY 2016</div><div class="title">Aculis facilisis massa</div>
  <div class="excerpt">Etiam eu urna Sed porta Suspendisse quam leo molestie sed luctus quis feugiat</div><div class="more">Read More</div></article>
<article class="blog-card abs" style="left:154px;top:1428px">
  <div class="photo" role="img" aria-label="Woman touching her face" style="background:linear-gradient(90deg,#f0ebe6,#e5c9b3 50%,#f3f0ec)"></div>
  <div class="date">02 MAY 2016</div><div class="title">Aculis facilisis massa</div>
  <div class="excerpt">Etiam eu urna Sed porta Suspendisse quam leo molestie sed luctus quis feugiat</div><div class="more">Read More</div></article>
<article class="blog-card abs" style="left:457px;top:1428px">
  <div class="photo" role="img" aria-label="Woman portrait on brown backdrop" style="background:linear-gradient(90deg,#8d7663,#e2c6ad 50%,#8d7663)"></div>
  <div class="date">02 MAY 2016</div><div class="title">Aculis facilisis massa</div>
  <div class="excerpt">Etiam eu urna Sed porta Suspendisse quam leo molestie sed luctus quis feugiat</div><div class="more">Read More</div></article>
<article class="blog-card abs" style="left:759px;top:1428px">
  <div class="photo" role="img" aria-label="Woman's waist in white underwear" style="background:linear-gradient(90deg,#e6e6e6,#eed7c6 50%,#e6e6e6)"></div>
  <div class="date">02 MAY 2016</div><div class="title">Aculis facilisis massa</div>
  <div class="excerpt">Etiam eu urna Sed porta Suspendisse quam leo molestie sed luctus quis feugiat</div><div class="more">Read More</div></article>

<section class="consult abs">
  <div class="model abs" role="img" aria-label="Blonde woman in white top against a pale sky"></div>
  <div class="brand-line abs">Velour Skinhaus</div>
  <h2 class="abs">DERMATOLOGIST CONSULTATION</h2>
  <p class="abs">Doctor Formulated, Freshly Handmade, Registered Pharmacy, Highest Ethical Standards.</p>
</section>

<h2 class="section-title articles-title abs">LATEST ARTICLES</h2>
<article class="article abs" style="left:148px">
  <div class="photo" role="img" aria-label="Smiling woman looking in a mirror" style="background:linear-gradient(90deg,#d9b7a4,#f3e2d6 55%,#ece6df)"></div>
  <div class="title">Article Tittle here</div>
  <div class="body">eu mattis in ante Morbi eget arcu Morbi porta libero id ullamcorper nonummy nibh ligula pulvinar</div></article>
<article class="article abs" style="left:618px">
  <div class="photo" role="img" aria-label="Smiling woman resting on a white bed" style="background:linear-gradient(90deg,#f5f5f5,#e9d3c2 60%,#f2f2f2)"></div>
  <div class="title">Article Tittle here</div>
  <div class="body">eu mattis in ante Morbi eget arcu Morbi porta libero id ullamcorper nonummy nibh ligula pulvinar</div></article>

<footer class="footer abs">
  <h4 class="abs" style="left:158px;top:45px">USEFULL LINKS</h4>
  <div class="links abs" style="left:158px;top:72px"><a>Home</a><a>About Us</a><a>Videos</a><a>Contact</a></div>
  <div class="links abs" style="left:306px;top:74px"><a>Site map</a><a>Press room</a><a>Privacy policy</a><a>Shipping &amp; return policy</a></div>
  <h4 class="abs" style="left:480px;top:45px">FOLLOW US</h4>
  <div class="socials abs"><span></span><span></span><span></span><span></span></div>
  <h4 class="abs" style="left:722px;top:45px">SIGN UP FOR NEWSLETTERS</h4>
  <div class="newsletter-note abs">Please sign up here for latest news</div>
  <div class="subscribe abs"><div class="field">EMAIL ADDRESS</div><div class="button">SUBSCRIBE</div></div>
  <div class="cards abs"><span></span><span></span><span></span><span></span><span></span></div>
  <div class="footer-rule abs"></div>
  <div class="copyright abs">© 2016 Company Name. All right reserved. Term of Use</div>
</footer>

</body>
</html>
```